Retail Sign for Houseplant Campaign

Sign will measure 3 to 4 foot tall by 22.2inches and place on rolling racks of houseplants for a retail promotion in The Birchwell Yard. The theme of the promotion will be "New Year, New You!" Selling points which should be on the sign are Houseplants give you a taste of nature, Houseplants boost air quality inside your home, Indoor plants reduce anxiety, Indoor plants make you more productive, Houseplants improve your concentration and memory.
Updates

Target Market(s)

People who love plants

Industry/Entity Type

Horticulture/ retail

Colors
00AB8E
00BBA5
67D7C9
C6EFE9
E9F9F6
59FF00
82FF00
B8FF75
E3FFCB
F4FFEA
FFF300
FFF600
FEFA6F
FFFEC7
FFFEE8

Requirements
Must have
• Must feel energetic and encourage people to buy plants. Should include 1-2 photos and the selling points listed

```html
<!DOCTYPE html>
<html lang="en">
<head>
<meta charset="utf-8">
<title>New Year, New You! – Houseplant Sign</title>
<link rel="stylesheet" href="https://fonts.googleapis.com/css2?family=Kaushan+Script&family=Itim&display=swap">
<style>
  :root {
    --backdrop: #8f8f8f;
    --pink: #f49197;
    --pink-shadow: #d9646d;
    --teal: #55d6c2;
    --teal-deep: #49c8b5;
    --teal-shadow: #2f9f8e;
    --yellow: #f5e85c;
    --lavender: #ddb6f0;
    --white: #ffffff;
    --photo-light: #f1f3f1;
    --photo-green: #9dbb86;
  }
  html, body {
    margin: 0;
    padding: 0;
    width: 840px;
    height: 1200px;
    overflow: hidden;
    background: var(--backdrop);
  }
  .sign-frame {
    position: absolute;
    left: 142.5px;
    top: 0;
    width: 555px;
    height: 1200px;
    overflow: hidden;
  }
  .sign {
    position: absolute;
    left: 0;
    top: 0;
    width: 737px;
    height: 1593px;
    transform: scale(0.7533);
    transform-origin: 0 0;
    font-family: "Itim", sans-serif;
    color: var(--white);
  }
  .sign-shapes {
    position: absolute;
    inset: 0;
    width: 737px;
    height: 1593px;
  }
  .headline {
    position: absolute;
    left: 0;
    top: 60px;
    width: 737px;
    margin: 0;
    font-family: "Kaushan Script", cursive;
    font-weight: 400;
    font-size: 122px;
    line-height: 118px;
    text-align: center;
    text-shadow: 4px 5px 0 var(--pink-shadow);
  }
  .headline span { display: block; }
  .headline .line-two { padding-left: 60px; }
  .benefits-kicker {
    position: absolute;
    left: 185px;
    top: 1022px;
    margin: 0;
    font-size: 50px;
    font-style: italic;
    letter-spacing: 1px;
    text-shadow: 2px 3px 0 var(--teal-shadow);
  }
  .benefits-title {
    position: absolute;
    left: 98px;
    top: 1060px;
    margin: 0;
    font-size: 104px;
    line-height: 110px;
    font-weight: 400;
    letter-spacing: 2px;
    text-shadow: 3px 4px 0 var(--teal-shadow);
  }
  .benefits-rule {
    position: absolute;
    left: 100px;
    top: 1173px;
    width: 537px;
    height: 3px;
    background: var(--white);
  }
  .benefit-list {
    position: absolute;
    left: 100px;
    top: 1202px;
    margin: 0;
    padding: 0;
    list-style: none;
    font-size: 33px;
    line-height: 43px;
    letter-spacing: 0.5px;
  }
  .benefit-list li {
    position: relative;
    padding-left: 46px;
    margin-bottom: 8px;
  }
  .benefit-list .tick {
    position: absolute;
    left: 0;
    top: 6px;
    width: 30px;
    height: 30px;
  }
</style>
</head>
<body>
  <div class="sign-frame">
    <div class="sign">
      <svg class="sign-shapes" viewBox="0 0 737 1593" xmlns="http://www.w3.org/2000/svg">
        <defs>
          <linearGradient id="photoTone" x1="0" y1="0" x2="1" y2="1">
            <stop offset="0" stop-color="var(--photo-light)"/>
            <stop offset="0.45" stop-color="#e4e9e0"/>
            <stop offset="0.75" stop-color="#d9c9c4"/>
            <stop offset="1" stop-color="#8f9ab0"/>
          </linearGradient>
        </defs>
        <rect class="lifestyle-photo" x="0" y="360" width="737" height="720" fill="url(#photoTone)"
              role="img" aria-label="Photo: a woman relaxing on the floor of a bright living room surrounded by potted houseplants"/>
        <path class="top-lavender" fill="var(--lavender)"
              d="M0,0 H737 V408 C720,428 690,473 620,488 C520,508 440,478 320,458 C200,443 100,463 0,518 Z"/>
        <path class="top-teal" fill="var(--teal)"
              d="M0,0 H737 V398 C720,418 690,463 620,478 C520,498 440,468 320,448 C200,433 100,453 0,508 Z"/>
        <path class="top-pink" fill="var(--pink)"
              d="M0,0 H737 V370 C710,390 660,422 580,430 C480,440 400,378 290,378 C200,380 100,420 0,500 Z"/>
        <path class="bottom-yellow" fill="var(--yellow)"
              d="M0,1030 C120,930 220,900 330,905 C450,910 560,960 737,895 V1593 H0 Z"/>
        <path class="bottom-lavender" fill="var(--lavender)"
              d="M0,1038 C120,972 230,958 360,988 C480,1018 600,1008 737,908 V1593 H0 Z"/>
        <path class="bottom-teal" fill="var(--teal)"
              d="M0,1046 C120,985 230,975 360,1005 C480,1035 610,1025 737,921 V1593 H0 Z"/>
        <circle class="bottom-bubble" cx="560" cy="1480" r="270" fill="var(--teal-deep)" opacity="0.45"/>
        <circle class="bottom-bubble" cx="120" cy="1620" r="230" fill="var(--teal-deep)" opacity="0.4"/>
      </svg>

      <h1 class="headline">
        <span class="line-one">New Year,</span>
        <span class="line-two">New You!</span>
      </h1>

      <p class="benefits-kicker">benefits of</p>
      <h2 class="benefits-title">Houseplants</h2>
      <div class="benefits-rule"></div>

      <ul class="benefit-list">
        <li><svg class="tick" viewBox="0 0 30 30"><circle cx="15" cy="15" r="13" fill="none" stroke="currentColor" stroke-width="2"/><path d="M9 15.5 L13.5 20 L21.5 11" fill="none" stroke="currentColor" stroke-width="2" stroke-linecap="round" stroke-linejoin="round"/></svg>Give you a taste of nature,</li>
        <li><svg class="tick" viewBox="0 0 30 30"><circle cx="15" cy="15" r="13" fill="none" stroke="currentColor" stroke-width="2"/><path d="M9 15.5 L13.5 20 L21.5 11" fill="none" stroke="currentColor" stroke-width="2" stroke-linecap="round" stroke-linejoin="round"/></svg>Boost air quality inside your home,</li>
        <li><svg class="tick" viewBox="0 0 30 30"><circle cx="15" cy="15" r="13" fill="none" stroke="currentColor" stroke-width="2"/><path d="M9 15.5 L13.5 20 L21.5 11" fill="none" stroke="currentColor" stroke-width="2" stroke-linecap="round" stroke-linejoin="round"/></svg>Indoor plants reduce anxiety,</li>
        <li><svg class="tick" viewBox="0 0 30 30"><circle cx="15" cy="15" r="13" fill="none" stroke="currentColor" stroke-width="2"/><path d="M9 15.5 L13.5 20 L21.5 11" fill="none" stroke="currentColor" stroke-width="2" stroke-linecap="round" stroke-linejoin="round"/></svg>Indoor plants<br>make you more productive,</li>
        <li><svg class="tick" viewBox="0 0 30 30"><circle cx="15" cy="15" r="13" fill="none" stroke="currentColor" stroke-width="2"/><path d="M9 15.5 L13.5 20 L21.5 11" fill="none" stroke="currentColor" stroke-width="2" stroke-linecap="round" stroke-linejoin="round"/></svg>Improve your<br>concentration and memory.</li>
      </ul>
    </div>
  </div>
</body>
</html>
```